QVR business card

Need a business card for a company that provides instructional design and elearning development services. The website is here: http://quorvane.studio/

I'm attaching a current logo, as well as the old business card design. While I like to keep it clean, the old design is too simplistic for my liking. The only idea I want to reuse from the old design is placing industry jargon on the back of the card, just need a better way to present it. But if you have other ideas for the back--feel free to experiment.

Please use the colors complementary to the color we have on the website. Thank you!

```html
<!DOCTYPE html>
<html lang="en">
<head>
<meta charset="utf-8">
<title>QVR business card</title>
<link rel="stylesheet" href="https://fonts.googleapis.com/css2?family=Open+Sans:wght@400;600;700&display=swap">
<style>
  :root {
    --teal: #10b3b0;
    --teal-dark: #0c9e9b;
    --tan: #dccf94;
    --ink: #3a3a3a;
    --card-white: #ffffff;
    --card-black: #111111;
    --line-light: #d8d8d8;
    --backdrop: #ece9e4;
  }
  * { margin: 0; padding: 0; box-sizing: border-box; }
  html, body {
    width: 1200px; height: 900px; overflow: hidden;
    background: var(--backdrop);
    font-family: "Open Sans", Arial, sans-serif;
  }
  .canvas { position: relative; width: 1200px; height: 900px; }

  .card {
    position: absolute; width: 560px; height: 320px; overflow: hidden;
    box-shadow: 0 6px 18px rgba(0,0,0,.18);
  }

  /* Back side */
  .card-back { left: 580px; top: 100px; background: var(--card-black); color: #fff; }
  .card-back .wordmark {
    position: absolute; left: 0; right: 0; top: 48px;
    display: flex; justify-content: center; align-items: center; gap: 14px;
  }
  .wordmark .mark-square { width: 22px; height: 22px; background: currentColor; }
  .wordmark .mark-name { font-size: 54px; font-weight: 700; letter-spacing: 4px; line-height: 1; }
  .card-back .help-rule {
    position: absolute; left: 40px; right: 40px; top: 158px;
    display: flex; align-items: center; gap: 14px;
  }
  .help-rule .rule { flex: 1; height: 1px; background: var(--line-light); }
  .help-rule .help-title { font-size: 15px; font-weight: 600; letter-spacing: .5px; }
  .card-back .jargon {
    position: absolute; top: 192px; left: 70px; right: 70px;
    display: flex; justify-content: space-between;
    font-size: 15px; line-height: 1.45;
  }
  .jargon .col-right { text-align: left; margin-top: 26px; }

  /* Front side */
  .card-front { left: 60px; top: 480px; background: var(--card-white); color: var(--ink); }
  .card-front .bands { position: absolute; inset: 0; }
  .card-front .holder-name {
    position: absolute; left: 68px; top: 26px;
    color: var(--teal); font-size: 18px; font-weight: 700;
  }
  .card-front .wordmark {
    position: absolute; left: 270px; top: 118px; color: var(--teal);
    display: flex; align-items: center; gap: 14px;
  }
  .contact {
    position: absolute; left: 26px; top: 150px; list-style: none;
    font-size: 14px; line-height: 1.55;
  }
  .contact li { display: flex; align-items: center; gap: 9px; }
  .contact svg { width: 12px; height: 12px; flex: none; }
</style>
</head>
<body>
<div class="canvas">

  <section class="card card-back" aria-label="Card back">
    <div class="wordmark">
      <span class="mark-square"></span>
      <span class="mark-name">QVR</span>
    </div>
    <div class="help-rule">
      <span class="rule"></span>
      <span class="help-title">HOW CAN WE HELP?</span>
      <span class="rule"></span>
    </div>
    <div class="jargon">
      <div class="col-left">
        Mobile Learning Scorm<br>
        Instructional Design Lms<br>
        Moocs Elearning Html5
      </div>
      <div class="col-right">
        Adult Learning Theory<br>
        Gamification Classroom<br>
        Xapi Blended Learning
      </div>
    </div>
  </section>

  <section class="card card-front" aria-label="Card front">
    <svg class="bands" viewBox="0 0 560 320" aria-hidden="true">
      <polygon points="0,18 26,18 0,44" fill="var(--tan)"/>
      <polygon points="30,18 52,18 40,46 18,46" fill="var(--teal)"/>
      <polygon points="0,258 190,258 172,286 0,286" fill="var(--tan)"/>
      <polygon points="196,266 560,266 560,320 162,320" fill="var(--teal)"/>
    </svg>

    <div class="holder-name">Maren Ostrowe</div>

    <ul class="contact">
      <li>
        <svg viewBox="0 0 12 12"><path d="M3 1 L5 3 L4 4.5 Q5 7 7.5 8 L9 7 L11 9 L9.5 11 Q3 10 1 3 Z" fill="var(--teal)"/></svg>
        415-302-7718
      </li>
      <li>
        <svg viewBox="0 0 12 12"><rect x="1" y="2.5" width="10" height="7" fill="var(--teal)"/><path d="M1 2.5 L6 6.5 L11 2.5" stroke="#fff" fill="none"/></svg>
        mostrowe@quorvane.studio
      </li>
      <li>
        <svg viewBox="0 0 12 12"><circle cx="6" cy="6" r="5" fill="var(--teal)"/><path d="M1 6 H11 M6 1 Q3 6 6 11 Q9 6 6 1" stroke="#fff" stroke-width=".8" fill="none"/></svg>
        www.quorvane.studio
      </li>
    </ul>

    <div class="wordmark">
      <span class="mark-square"></span>
      <span class="mark-name">QVR</span>
    </div>
  </section>

</div>
</body>
</html>
```